Redesign This Psychology Website

We would like a slight redesign of this successful psychology (relationship counselling) website:

www.TheKelvaleClinic.com.au

We are updating the website, and we'd like a slight refresh of the design and style.

Please keep to very similar colours, and use the same logo. We're looking for around 10 page templates, however the main one is the home page.

Keep in mind, this website already converts quite well, so we want a new, fresh design in keeping with this one. Please don't bother designing something too extremely different.

thanks :)

Target Market(s)

couples who are looking for relationship counselling. Men and women, 25 - 70, across Australia

Industry/Entity Type

Psychology

Number of Pages Required

5+ page

Font styles to use
Sans Serif

Colors
87cfc6
b7a5cd
ec1f27
ffffff
cee9f5

Requirements
Must have
• a similar look to the current design, just looking for a slight refresh.
• Search bar
• Areas for lots of photos
• same logo
• lots of content areas
Nice to have
• great content areas, where we can display a lot of content and our areas.
Should not have
• no colors like orange, etc.
• should not have a totally different feel.

```html
<!DOCTYPE html>
<html lang="en">
<head>
<meta charset="utf-8">
<title>Our Blogs – The Kelvale Clinic</title>
<link href="https://fonts.googleapis.com/css2?family=Open+Sans:wght@400;600;700&family=Nunito+Sans:wght@400;600;700&display=swap" rel="stylesheet">
<style>
:root{
  --teal:#87cfc6;
  --teal-dark:#3fb0a4;
  --lilac:#b7a5cd;
  --red:#ec1f27;
  --sky:#cee9f5;
  --white:#ffffff;
  --ink:#333333;
  --body:#666666;
  --muted:#8a8a8a;
  --line:#dddddd;
  --bar:#eeeeee;
  --foot:#f2f2f2;
}
*{box-sizing:border-box;margin:0;padding:0}
html,body{width:1200px;height:3644px;overflow:hidden}
body{position:relative;background:var(--white);font-family:"Open Sans",Arial,sans-serif;color:var(--body)}
a{color:inherit;text-decoration:none}

.top-bar{position:absolute;left:0;top:0;width:1200px;height:34px;background:var(--bar);font-size:12px;color:#777}
.top-bar .associate{position:absolute;left:134px;top:9px}
.top-bar .util-links{position:absolute;right:145px;top:0;display:flex;height:34px}
.top-bar .util-links a{padding:9px 12px;border-left:1px solid #dcdcdc}

.site-header{position:absolute;left:0;top:34px;width:1200px;height:126px}
.brand{position:absolute;left:117px;top:26px;display:flex;align-items:center;gap:12px}
.brand-dot{width:40px;height:40px;border-radius:50%;background:var(--teal-dark)}
.brand-name{font-family:"Nunito Sans",sans-serif;font-weight:700;font-size:30px;color:var(--teal-dark);line-height:1}
.brand-tag{position:absolute;left:169px;top:78px;font-size:13px;color:var(--teal-dark)}
.search{position:absolute;left:457px;top:51px;width:355px;height:39px;border:1px solid #d5d5d5;display:flex;align-items:center;padding-left:12px;gap:9px;font-size:12px;color:#aaa}
.call{position:absolute;right:145px;top:38px;text-align:right}
.call-label{font-size:15px;color:var(--teal)}
.call-number{display:flex;align-items:center;gap:6px;font-size:24px;font-weight:600;color:var(--teal-dark)}

.main-nav{position:absolute;left:0;top:160px;width:1200px;height:68px;background:linear-gradient(180deg,#9ad8d0,var(--teal))}
.main-nav ul{list-style:none;display:flex;height:68px;margin-left:110px}
.main-nav li{display:flex;align-items:center;padding:0 12px;border-right:1px solid rgba(255,255,255,.5);color:var(--white);font-weight:700;font-size:13.5px;line-height:1.15;text-transform:uppercase}
.main-nav li:last-child{border-right:0}

.hero{position:absolute;left:0;top:228px;width:1200px;height:326px;background:linear-gradient(100deg,#b98a6e 0%,#d8b59a 35%,#efd9c6 55%,#c6906e 80%,#a56a4f 100%)}
.hero h1{position:absolute;left:126px;top:165px;font-family:"Nunito Sans",sans-serif;font-weight:600;font-size:40px;color:var(--white);letter-spacing:1px}

.article{position:absolute;left:129px;top:0;width:583px;font-size:13px;line-height:20px}
.article h2{font-family:"Nunito Sans",sans-serif;font-weight:600;color:var(--red);font-size:25px;line-height:30px}
.article .title{position:absolute;top:604px;left:0;color:#222;font-size:27px}
.article p{margin-bottom:10px}
.block{position:absolute;left:0;width:583px}
.intro-photo{position:absolute;left:5px;top:654px;width:298px;height:211px;background:linear-gradient(135deg,#c9ccd1,#8e949c)}
.intro-text{position:absolute;left:323px;top:650px;width:260px}
.sacrificial-list{list-style:none;margin-top:20px;font-size:12.5px;line-height:18px}
.sacrificial-list li{margin-bottom:8px}

.finder{position:absolute;left:768px;top:598px;width:301px;height:369px;background:var(--lilac);color:var(--white);padding:22px 25px}
.finder h3{font-family:"Nunito Sans",sans-serif;text-align:center;font-size:22px;line-height:26px;font-weight:700}
.finder .rule{width:110px;height:1px;background:rgba(255,255,255,.8);margin:4px auto 14px}
.finder label{display:block;font-size:12px;margin:10px 0 5px}
.field{height:30px;background:var(--white);border-radius:2px;font-size:11px;color:#888;padding:7px 10px;display:flex;justify-content:space-between}
.finder .submit{margin-top:24px;height:38px;background:var(--red);border-radius:2px;text-align:center;font-weight:700;font-size:15px;line-height:38px}

.related{position:absolute;left:778px;top:990px;width:298px}
.related-card{display:flex;height:115px;margin-bottom:14px;border:1px solid var(--line);background:var(--white)}
.related-card .thumb{width:152px;height:113px;flex:none}
.related-card .info{padding:12px 10px;font-size:13px;line-height:17px;color:#333}
.related-card .more{display:block;margin-top:6px;font-size:11px;color:var(--teal-dark)}

.site-footer{position:absolute;left:0;top:3273px;width:1200px;height:299px;background:var(--foot)}
.foot-brand{position:absolute;left:134px;top:75px}
.foot-brand .brand-row{display:flex;align-items:center;gap:12px}
.foot-brand .brand-tag{position:static;display:block;margin:8px 0 0 52px}
.foot-col{position:absolute;top:70px;font-size:12px;line-height:28px;color:#666}
.foot-col h4{font-size:15px;font-weight:700;color:var(--teal-dark);line-height:22px;margin-bottom:6px}
.socials{display:flex;gap:8px;margin-top:10px}
.socials span{width:30px;height:30px;border-radius:50%}
.copyright{position:absolute;left:0;top:3572px;width:1200px;height:72px;background:#e6e6e6;text-align:center;font-size:11px;line-height:72px;color:#888}
</style>
</head>
<body>

<div class="top-bar">
  <a class="associate" href="#">Join Our Associate Program →</a>
  <nav class="util-links"><a href="#">Home</a><a href="#">Cart</a><a href="#">Blog</a><a href="#">Resources</a><a href="#">Contact</a></nav>
</div>

<header class="site-header">
  <div class="brand"><span class="brand-dot"></span><span class="brand-name">The Kelvale Clinic</span></div>
  <span class="brand-tag">helping you create loving relationships</span>
  <div class="search">
    <svg width="14" height="14" viewBox="0 0 14 14"><circle cx="6" cy="6" r="4.5" fill="none" stroke="#999" stroke-width="1.5"/><line x1="9.3" y1="9.3" x2="13" y2="13" stroke="#999" stroke-width="1.5"/></svg>
    Search here
  </div>
  <div class="call">
    <div class="call-label">Call Us Now</div>
    <div class="call-number">
      <svg width="20" height="20" viewBox="0 0 24 24"><path d="M6.6 10.8a15 15 0 0 0 6.6 6.6l2.2-2.2a1 1 0 0 1 1-.25 11.4 11.4 0 0 0 3.6.57 1 1 0 0 1 1 1V20a1 1 0 0 1-1 1A17 17 0 0 1 3 4a1 1 0 0 1 1-1h3.5a1 1 0 0 1 1 1c0 1.25.2 2.45.57 3.57a1 1 0 0 1-.25 1z" fill="var(--red)"/></svg>
      1300 555 014
    </div>
  </div>
</header>

<nav class="main-nav">
  <ul>
    <li>Counselling<br>Types</li>
    <li>Relationship Counselling<br>Locations</li>
    <li>Sex Therapy<br>Locations</li>
    <li>About Us</li>
    <li>Quizzes</li>
    <li>FAQ's</li>
    <li>Contact</li>
  </ul>
</nav>

<section class="hero" role="img" aria-label="Photo of a smiling couple making a heart shape with their hands">
  <h1>OUR BLOGS</h1>
</section>

<article class="article">
  <h2 class="title">Why am I with a Narcissist?</h2>
  <div class="intro-photo" role="img" aria-label="Photo of a thoughtful woman sitting with her arms folded"></div>
  <div class="intro-text">
    <p>You may be wondering why anyone would be masochistic enough to ever get themselves into a relationship with someone who has so many characteristics of a Narcissist and who leaves you feeling so dreadful?</p>
    <p>But the truth is that things start off very differently. The narcissist is an absolute</p>
  </div>
  <div class="block" style="top:870px">
    <p>perfect delight right from the first day you start dating: wining, dining and gifts, nothing is too much trouble for him/her; your every whim is his/her desire; he/she is truly the perfect and charming partner.</p>
    <p>Finding yourself in a "whirlwind romance", he/she will appear to be all you have ever wanted in a partner and in a relationship, so much so that it all seems almost "too good to be true", which of course it is.</p>
    <p>At this stage you are his/her "prey", and he/she is an expert at contriving his/her behaviour to impress you, and being sensitive to what you are wanting, until he/she has snared you. He/she has you in his/her sights as his/her next source of Narcissistic supply, so all his/her energies, shows of love, affection and fake empathy are committed to lure you.</p>
  </div>

  <div class="block" style="top:1200px">
    <h2>The transition</h2>
    <p style="margin-top:8px">However this "impress your socks off" stage doesn't last, and once he/she now feels secure in the relationship (this happens most commonly at the 3 major transitions: when you move in together, when you get married, or when you start having children) there is now no longer a need for making an effort.</p>
    <p>Without realizing it, you are now owned by him/her; you have crossed over into his/her self-definition boundary. With this transition comes the expectation that you now are an extension of him/her.</p>
    <p>This dumbfounding change can be made almost overnight, or at a more gradual pace, but change it does.</p>
  </div>

  <div class="block" style="top:1492px">
    <h2>The “Bubble”</h2>
    <p style="margin-top:8px">One man described that for him it felt like he and his wife were in a big bubble that he had created as his reality. His wife had freedom, and all was happy, as long as she stayed in the bubble. "There was room to move about so the illusion of freedom seemed real to her. But when she expressed an idea of her own, or any feelings, it was like she was stepping out of his bubble and stepping into her own. But he did not want her out there. He feared being alone with himself. He feared being with his feelings. So he tried to pull her back into his bubble, or worse, injure her so she could never leave, or worse yet, disorient her so she can never find her way out." Whatever control measure or verbal abuse it took, getting her back inside the bubble where he could feel safe again was his primary objective.</p>
    <p>The Narcissist usually feels a great and strong love for his/her partner, but this is in essence a control connection rather than real love. There is no regard for his/her individuality, no empathy or understanding, and usually an angry assault or the silent treatment, every time he/she shows any signs of separateness.</p>
    <p>This leaves you feeling shunned, negated, unseen, unheard, trivialised, and, as a result, also very confused, sad, and often outraged that you have been so invaded or negated, every time you express your individuality.</p>
  </div>

  <div class="block" style="top:1980px">
    <h2>How did you become a willing victim? Why you?</h2>
    <p style="margin-top:8px">If you find yourself in a relationship with a Narcissist, at some stage you might wonder why you? What does this say about you, your tolerance for pain and your sanity?</p>
    <p>It is true that there is a particular kind of person that finds themself with a Narcissist, at least often well beyond the first indication that there is an underlying nastiness in him.</p>
    <p>The kind of person who seems to unwittingly attract a Narcissist is someone who has what I call a "Sacrificial Self", (which has also been referred to as Co-dependent or compliant or a deflated false self). This means you may have a tendency to unnecessarily attribute blame to yourself in situations when you haven't done anything wrong.</p>
    <p>In Transactional Analysis terms, a Narcissist's underlying Life position is I'm Ok, You're Not OK, whereas a Sacrificial's underlying Life Position is I'm Not OK, You're OK.</p>
  </div>

  <div class="block" style="top:2345px">
    <h2>How Can I tell if I am a Sacrificial Self?</h2>
    <p style="margin-top:12px">Here again, it is important to understand that there are varying degrees of this kind of Self, as there are with a Narcissistic self.</p>
    <p>A Sacrificial person is characterised by:</p>
    <ol class="sacrificial-list">
      <li>1. A deflated False self</li>
      <li>2. Your feelings are often numbed, and you are not always aware of them in the moment</li>
      <li>3. You experience a lack of awareness of your own needs.</li>
      <li>4. You also are not good at knowing what your real wants are.</li>
      <li>5. You often feel guilt and shame for not being able to meet people's needs</li>
      <li>6. Your loved ones withdrawing their love, or threatening to withdraw it, triggers a lot of anxiety in you</li>
      <li>7. You are often not truly in touch with your own deeper truth</li>
      <li>8. You can often prefer to live in a fantasy where you believe your partner truly loves you, even though much of the evidence can show you the contrary</li>
      <li>9. You have experienced poor self esteem over your life</li>
      <li>10. You are not always able to see where your boundaries should and shouldn't be</li>
      <li>11. You are not often able to assertively stand up to those you love</li>
      <li>12. You can at times feel a vague sense of depression and emptiness</li>
      <li>13. You can lack a sense of a healthy entitlement in your relationships</li>
      <li>14. You can often feel frustrated and dissatisfied with your life</li>
      <li>15. There are times when you feel your life has no meaning</li>
      <li>16. You have an underlying belief that I must sacrifice myself to survive in a relationship</li>
      <li>17. In a relationship, you may be responsive and reactive to your partner, rather than proactive</li>
      <li>18. You excessively blame yourself in your relationship</li>
      <li>19. You often have the underlying sense that if something is going right for you at the moment, it probably won't last.</li>
      <li>20. You tend to take more than your fair share of responsibility in a relationship, to make it better and improve it.</li>
    </ol>
  </div>
</article>

<aside class="finder">
  <h3>Find Our Psychologist<br>Near You</h3>
  <div class="rule"></div>
  <label>Type of Counselling</label>
  <div class="field"><span>Select</span><span>⌄</span></div>
  <label>Location</label>
  <div class="field"></div>
  <label>Postcode</label>
  <div class="field"></div>
  <div class="submit">SEARCH</div>
</aside>

<div class="related">
  <div class="related-card"><div class="thumb" role="img" aria-label="Photo of two hands reaching for each other" style="background:linear-gradient(135deg,#d7c1ad,#8f7866)"></div><div class="info">What can I do if I'm living with a Narcissist?<span class="more">Read More</span></div></div>
  <div class="related-card"><div class="thumb" role="img" aria-label="Photo of a man looking troubled" style="background:linear-gradient(135deg,#7c6a62,#3b302c)"></div><div class="info">Are You Living With a Steamroller?<span class="more">Read More</span></div></div>
  <div class="related-card"><div class="thumb" role="img" aria-label="Photo of a couple talking on a couch" style="background:linear-gradient(135deg,#cdbfb4,#6d5c54)"></div><div class="info">Did Your Relationship Start on Rocky Ground?<span class="more">Read More</span></div></div>
  <div class="related-card"><div class="thumb" role="img" aria-label="Photo of a woman sitting alone in thought" style="background:linear-gradient(135deg,#c9ccd1,#8e949c)"></div><div class="info">Why am I with a Narcissist?<span class="more">Read More</span></div></div>
  <div class="related-card"><div class="thumb" role="img" aria-label="Photo of a couple in a counselling session" style="background:linear-gradient(135deg,#e1d3c4,#9a8572)"></div><div class="info">Letter for a Partner Doubtful About Relationship Counselling<span class="more">Read More</span></div></div>
  <div class="related-card"><div class="thumb" role="img" aria-label="Photo of a couple embracing outdoors" style="background:linear-gradient(135deg,#d9b48f,#8a5a3c)"></div><div class="info">What Are You Like In a Relationship?<span class="more">Read More</span></div></div>
  <div class="related-card"><div class="thumb" role="img" aria-label="Photo of a man and woman in conversation" style="background:linear-gradient(135deg,#6f6d73,#2f2d33)"></div><div class="info">How Do I Know If I'm With a Narcissist?<span class="more">Read More</span></div></div>
  <div class="related-card"><div class="thumb" role="img" aria-label="Photo of a laughing couple" style="background:linear-gradient(135deg,#e6c9b4,#a9735a)"></div><div class="info">Do You Wonder Why You and Your Partner Are Together?<span class="more">Read More</span></div></div>
  <div class="related-card"><div class="thumb" role="img" aria-label="Photo of a businessman working at a desk" style="background:linear-gradient(135deg,#b9c2cc,#56616d)"></div><div class="info">Is Your Pursuit of Success Sabotaging Your Relationships That Matter Most?<span class="more">Read More</span></div></div>
</div>

<footer class="site-footer">
  <div class="foot-brand">
    <div class="brand-row"><span class="brand-dot"></span><span class="brand-name">The Kelvale Clinic</span></div>
    <span class="brand-tag">helping you create loving relationships</span>
  </div>
  <div class="foot-col" style="left:452px">
    <h4>QUICK LINKS</h4>
    <a href="#">Home</a><br><a href="#">About Us</a><br><a href="#">Our Blogs</a><br><a href="#">Shop Cart</a><br><a href="#">Contact Us</a>
  </div>
  <div class="foot-col" style="left:620px">
    <h4>RESOURCES</h4>
    <a href="#">Counselling Type</a><br><a href="#">Sex Therapy</a><br><a href="#">Quizzes</a><br><a href="#">FAQ</a><br><a href="#">Relationship Counselling</a>
  </div>
  <div class="foot-col" style="left:824px">
    <h4>CONTACT US</h4>
    42 Harbour Lane Suite 12<br>1300 555 014<br>Email: info@kelvaleclinic.com.au
    <div class="socials"><span style="background:#55acee"></span><span style="background:#3b5998"></span><span style="background:#0e76a8"></span><span style="background:#dd4b39"></span></div>
  </div>
</footer>
<div class="copyright">© 2017 Company Name. All rights reserved</div>

</body>
</html>
```